RW Holloway LLC Business Card - Civil Engineering & Consulting Firm

We need a Business Card that is elegant, and masculine.  It is our Professional Civil Engineering & Consulting Company located in San Antonio TX (Not s construction or builder firm- no gears & no tool images please). We provide civil engineering services including  commercial site plans, grading and drainage plans, utility plans, hydraulics and hydrology, land planning, utility coordination, and other general civil engineering services related to commercial and residential development.
We have 2 existing Logos. We would like to convey reliability, strength, trustworthiness and attention to detail.  Blues and orange tones as per logo We are OK with the use of a darker blue in the mix.  We have 2 logo versions - Full Company Name Logo to go on the back of card, & Small Icon Logo for the front w/ personal Info.

Target Market(s)
Architects, Real Estate Developers, Other Strctural Engineers, Surveyers, General Contractors
Industry/Entity Type
Professional Civil Engineering
Contact Information for Business Card
Name, Position, Address, Cell & Office #, email, and company website
Font styles to use
Other font styles liked:
- Avian
Requirements
Should not have
- No Tools, No Gears, no Cranes, or Construction Equipment.

```html
<!DOCTYPE html>
<html lang="en">
<head>
<meta charset="utf-8">
<title>RW Holloway LLC – Business Card</title>
<link rel="stylesheet" href="https://fonts.googleapis.com/css2?family=Arimo:wght@400;700&display=swap">
<style>
  :root {
    --stage: #161616;
    --card: #2e2e30;
    --card-edge: #e07f1a;
    --orange: #f08a1c;
    --blue: #5b9bd5;
    --ink: #f2f2f2;
    --pattern-dark: #262628;
    --pattern-light: #343437;
  }
  * { box-sizing: border-box; margin: 0; padding: 0; }
  html, body {
    width: 1200px; height: 963px; overflow: hidden;
    background: var(--stage);
    font-family: "Arimo", Arial, sans-serif;
  }
  .stage {
    position: relative; width: 1200px; height: 963px;
    display: flex; flex-direction: column; align-items: center; justify-content: center; gap: 64px;
  }
  .card {
    position: relative; width: 600px; height: 343px;
    background: var(--card);
    border-radius: 22px;
    box-shadow: 0 4px 0 var(--card-edge), 0 18px 40px rgba(0,0,0,.55);
    overflow: hidden;
  }
  .brand-name { color: var(--blue); font-family: "Arimo", Arial, sans-serif; font-weight: 700; letter-spacing: .5px; white-space: nowrap; }
  .brand-square { width: 14px; height: 14px; background: var(--orange); flex: none; }

  /* front */
  .card-front { display: flex; align-items: center; }
  .brand-mark {
    width: 270px; display: flex; align-items: center; justify-content: center; gap: 10px;
  }
  .brand-mark .brand-name { font-size: 20px; }
  .contact { padding-left: 20px; color: var(--ink); font-size: 17px; line-height: 1.3; }
  .contact .person { color: var(--orange); font-weight: 700; font-size: 21px; text-transform: uppercase; letter-spacing: .3px; }
  .contact .role { margin-bottom: 14px; }
  .contact .address { margin-bottom: 14px; }
  .contact ul { list-style: none; }
  .contact li { display: flex; align-items: center; gap: 10px; }
  .contact li svg { width: 14px; height: 14px; flex: none; }

  /* back */
  .back-pattern {
    position: absolute; inset: 0;
    background: linear-gradient(135deg, var(--pattern-dark), var(--pattern-light) 50%, var(--pattern-dark));
  }
  .back-lockup {
    position: absolute; right: 48px; top: 50%; transform: translateY(-50%);
    display: flex; align-items: center; gap: 12px;
  }
  .back-lockup .brand-square { width: 20px; height: 20px; }
  .back-lockup .brand-name { font-size: 30px; }
</style>
</head>
<body>
<main class="stage">
  <section class="card card-front">
    <div class="brand-mark">
      <span class="brand-square"></span>
      <span class="brand-name">RW Holloway LLC</span>
    </div>
    <div class="contact">
      <p class="person">Daniel Reyes</p>
      <p class="role">Manager</p>
      <p class="address">Your address, city<br>state, ZIP 0000</p>
      <ul>
        <li><svg viewBox="0 0 16 16"><path d="M4 1l3 3-2 2a9 9 0 0 0 5 5l2-2 3 3-2 3C6 14 2 10 1 3z" fill="var(--orange)"/></svg>123-456-2100</li>
        <li><svg viewBox="0 0 16 16"><rect x="4" y="1" width="8" height="14" rx="1.5" fill="none" stroke="var(--orange)" stroke-width="1.6"/><circle cx="8" cy="12.5" r="1" fill="var(--orange)"/></svg>123-456-2100</li>
        <li><svg viewBox="0 0 16 16"><rect x="1" y="3" width="14" height="10" fill="none" stroke="var(--orange)" stroke-width="1.6"/><path d="M1 3l7 6 7-6" fill="none" stroke="var(--orange)" stroke-width="1.6"/></svg>youremail@example.com</li>
        <li><svg viewBox="0 0 16 16"><circle cx="8" cy="8" r="6.5" fill="none" stroke="var(--orange)" stroke-width="1.6"/><path d="M1.5 8h13M8 1.5c-3 3-3 10 0 13M8 1.5c3 3 3 10 0 13" fill="none" stroke="var(--orange)" stroke-width="1.2"/></svg>www.yourwebsite.com</li>
      </ul>
    </div>
  </section>

  <section class="card card-back">
    <div class="back-pattern" role="img" aria-label="Embossed repeating brand pattern covering the card"></div>
    <div class="back-lockup">
      <span class="brand-square"></span>
      <span class="brand-name">RW Holloway LLC</span>
    </div>
  </section>
</main>
</body>
</html>
```